Bold, Modern, Clean "Kestrelwaymassage.com" website

Why we stand out?
We are a male and female mobile massage team. Our names are Paul and Lina. 
Kestrel Way is a Seattle based mobile massage service. Our massage is offered to the community with a goal of facilitating balance within each individual. We specialize in integrated Pain management, and sports/medical massage therapy. Every client's first assessment is attended by our male and female massage therapist team. Depending on the goals identified for an individual determines which therapist will be assigned to provide treatment, if not both.

Our passion...
Here at Kestrel Way, we have a great passion for Postural Resoration and how it is integrated into an individual's Massage treatment. We pride ourselves in being natural facilitators of healing, which takes the ego of the therapist out of the client's healing process. We strive to deliver the best massage possible by including modalities such as Neuromuscular, Myofascial release, spontaneous muscle release, postural restoration, orthopedic, and medical massage.

Our education...

We are both Graduates of Venmora, school of massage therapy. We have continuing education in medical massage, myofacial release, trigger point therapy, postural restoration, anatomy, and spontaneous muscle release. Lina is also a Certified Yoga Instructor, which amplifies her experience with flexibility and strength as it pertains to each individual. Paul's passion is Massage, stretching, and strength training to encourage postural restoration and realignment.

Our rates-

Our rates are $75/ 60 minutes, $95/ 90 minutes, and $120/ 120 minutes.

Education-
Both Lina and I worked as behavioral health professionals that specialized in life skills mentoring for youth who had experienced different types of trauma. This led us both to want to help others in a different environment, where individuals can be empowered to take responsibility over their own healing. To us, massage is a type of manipulation physical therapy, that encourages healing on many levels.

Advice to any massage client-
The most important thing to 'us', as Licenced providers is to get you on to our table to show you our skills. But a good therapist never forgets that it's not about what we do for you, but what we can facilitate for you. Your health and healing has nothing to do with us. It is yours, not ours. Identify what your goals are with any Therapist, and know what the end looks like. Progress should be tangible, such as range of motion, and decreased pain.

Lina and Paul at Kestrel Way are awesome! I recently had open heart surgery, and Lina worked on me to increase my range of motion while helping with the pinched nerve from my arm being in the same position for so long during my surgery. My wife drives a lot for work, and Paul has helped decrease her neck and lower back pain immensely. They are seriously the best therapists I have ever worked with. I would recommend them to anyone who needs anything from stress relief to a medical massage treatment. They are professional, up beat, easy going, and always on time. And, I love that they meet us where ever we like! We did a staycation recently, where they came to our hotel to give us relaxation massages. Although usually they come to our home, where we focus on pain related issues. We will continue to work with them for a long, long time.

Target Market(s)

Mobile massage therapy clients

Industry/Entity Type

Massage Therapy

Coding

Coded - Design and coding required

Number of Pages Required

1 page

Font styles to use
Serif
Sans Serif

Requirements
Must have
• Please add or remove any information that would help the presentation of our website. Our logo is posted below, please include into the website.
• Please include a contact field that includes, kestrelwaymassage@fernmail.net,
• (206) 555-0148
• We have also included our own stock photos, as well as a photo of Paul and Lina. Please include a cropped photo of both massage therapists.

```html
<!DOCTYPE html>
<html lang="en">
<head>
<meta charset="utf-8">
<title>Kestrel Way – Mobile Massage</title>
<link rel="stylesheet" href="https://fonts.googleapis.com/css2?family=Raleway:wght@300;400;500;600;700&family=Lobster&family=Montserrat:wght@600;700&display=swap">
<style>
:root{
  --ink:#2b2b2b;
  --muted:#555;
  --nav:#141414;
  --cyan:#07c9d6;
  --teal:#0b8f96;
  --navy:#0f1a8c;
  --brand:#1b2fb8;
  --page:#f7f7f7;
  --white:#ffffff;
  --footer:#3a2c24;
}
*{box-sizing:border-box;margin:0;padding:0}
html,body{width:1200px;height:2200px;overflow:hidden}
body{position:relative;background:var(--page);font-family:'Raleway',sans-serif;color:var(--ink)}
.abs{position:absolute}

/* header */
.topbar{left:0;top:0;width:1200px;height:76px;background:var(--white)}
.contact-line{right:138px;font-size:15px;color:#333;display:flex;align-items:center;gap:8px}
.contact-line svg{width:18px;height:18px}
.navbar{left:0;top:76px;width:1200px;height:46px;background:var(--nav);border-bottom:3px solid var(--cyan)}
.nav-links{position:absolute;left:360px;top:0;display:flex;height:46px;align-items:center;list-style:none}
.nav-links li{color:#e8e8e8;font-size:15px;padding:0 20px;border-left:1px solid #2c2c2c;position:relative}
.nav-links li:first-child{border-left:none}
.nav-links li.active::after{content:"";position:absolute;left:50%;bottom:-16px;margin-left:-7px;border:7px solid transparent;border-bottom-color:var(--cyan)}
.brand-panel{left:142px;top:0;width:151px;height:161px;background:var(--white);box-shadow:0 2px 6px rgba(0,0,0,.25);display:flex;align-items:center;justify-content:center;z-index:3}
.brand-mark{width:136px;height:136px;border-radius:50%;background:var(--brand);display:flex;align-items:center;justify-content:center;text-align:center;color:var(--white);font-weight:700;font-size:22px;line-height:1.05}

/* hero */
.hero{left:0;top:125px;width:1200px;height:450px;background:linear-gradient(90deg,#d9b48f 0%,#c9c060 35%,#e2ea4a 60%,#d8dc5a 80%,#c8c8b0 100%)}
.hero-title{right:175px;top:160px;text-align:right;font-family:'Lobster',sans-serif;font-size:54px;line-height:1.1}
.hero-title .w{color:var(--white)}
.hero-title .n{color:var(--navy)}
.hero-rule{left:825px;top:295px;width:218px;height:1px;background:#fff}
.hero-tag{left:825px;top:308px;width:218px;text-align:center;font-size:22px;color:#1a1a1a;font-weight:500}
.hero-arrow{width:38px;height:38px;border-radius:50%;background:rgba(255,255,255,.55);display:flex;align-items:center;justify-content:center}

/* inquiry */
.inquiry{left:744px;top:512px;width:318px;height:498px;background:var(--white);border-radius:8px;box-shadow:0 2px 8px rgba(0,0,0,.15);z-index:2}
.inquiry h2{font-weight:400;font-size:27px;text-align:center;margin-top:16px}
.inquiry .lead{text-align:center;font-size:11.5px;font-weight:600;margin-top:4px}
.field{position:absolute;left:22px;width:274px;height:32px;border:1px solid #d4d4d4;border-radius:4px;font-size:12px;color:#666;padding:8px 16px}
.field.area{height:120px}
.select-caret{position:absolute;right:12px;top:8px;width:16px;height:14px;border:1px solid #888;background:#eee}
.cta{position:absolute;left:22px;top:406px;width:274px;height:44px;background:var(--cyan);border-radius:6px;color:var(--white);font-weight:700;font-size:16px;display:flex;align-items:center;justify-content:center}
.note{position:absolute;left:0;top:463px;width:318px;text-align:center;font-size:10px;color:#888;font-weight:600}

/* about */
.about-title{left:139px;top:594px;font-size:38px;font-weight:400}
.rule{height:1px;background:#333}
.rule .accent{position:absolute;left:0;top:-1px;width:120px;height:3px;background:var(--cyan)}
.about-text{left:139px;top:677px;width:550px;font-size:15px;line-height:24px;color:var(--muted)}
.point{left:139px;display:flex;gap:15px}
.point-icon{width:36px;height:36px;border-radius:50%;background:var(--cyan);flex:none;display:flex;align-items:center;justify-content:center}
.point h3{font-size:18px;font-weight:700;color:#111}
.point p{font-size:14px;color:var(--muted);margin-top:2px}
.point b{color:#111;text-decoration:underline;font-weight:700}
.btn-view{left:540px;top:1025px;width:120px;height:33px;background:var(--cyan);color:var(--white);font-weight:700;font-size:15px;display:flex;align-items:center;justify-content:center;border-radius:2px}

/* prices */
.prices{left:0;top:1086px;width:1200px;height:402px;background:var(--teal)}
.section-title{width:1200px;left:0;text-align:center;font-weight:400}
.prices .section-title{color:var(--white);font-size:38px;top:18px}
.price-card{top:113px;width:291px;height:234px;background:var(--white);border-radius:16px;text-align:center}
.price-card h3{font-family:'Montserrat',sans-serif;font-size:30px;margin-top:24px;color:#222}
.price-card .rate{font-size:19px;margin:6px 16px 0;padding-bottom:10px;border-bottom:1px solid #333}
.price-card .kind{font-size:18px;margin-top:18px}
.price-card .desc{font-size:12.5px;color:#555;margin:6px 10px 0;line-height:17px}
.badge{position:absolute;left:50%;bottom:-30px;margin-left:-30px;width:60px;height:60px;border-radius:50%;background:var(--white);display:flex;align-items:center;justify-content:center}
.badge span{width:32px;height:32px;border-radius:50%;background:#2a2a2a;color:#fff;font-weight:700;font-size:17px;display:flex;align-items:center;justify-content:center}

/* testimonials */
.reviews-title{top:1508px;font-size:38px}
.client-photo{left:151px;top:1593px;width:152px;height:152px;border-radius:50%;border:7px solid var(--cyan);background:radial-gradient(circle at 50% 40%,#a89a90,#3b3b3b);}
.client-name{left:326px;top:1608px;font-size:27px;font-weight:700}
.client-role{left:326px;top:1647px;font-size:16px;color:#444}
.client-quote{left:326px;top:1674px;width:740px;font-size:16px;line-height:24px;color:#444}
.dots{left:575px;top:1764px;display:flex;gap:5px}
.dots i{width:13px;height:13px;border-radius:50%;border:2px solid var(--cyan)}
.dots i.on{background:var(--cyan)}

/* footer */
.footer{left:0;top:1837px;width:1200px;height:363px;border-top:5px solid var(--cyan);background:linear-gradient(90deg,#6b5a4c 0%,#3a2c24 35%,#2f231d 65%,#5a4536 100%)}
.foot-mark{left:553px;top:1863px;width:96px;height:96px;border-radius:50%;background:var(--brand);color:#fff;font-weight:700;font-size:16px;display:flex;align-items:center;justify-content:center;text-align:center;line-height:1.05}
.foot-nav{left:0;top:1976px;width:1200px;display:flex;justify-content:center;gap:52px;list-style:none;color:#fff;font-size:13px;letter-spacing:.3px}
.foot-rule{height:1px;background:rgba(255,255,255,.75)}
.foot-phone{left:0;top:2030px;width:1200px;display:flex;justify-content:center;align-items:center;gap:10px;color:var(--cyan);font-family:'Montserrat',sans-serif;font-weight:700;font-size:29px}
.socials{left:0;top:2104px;width:1200px;display:flex;justify-content:center;gap:6px}
.socials i{width:28px;height:28px;border-radius:50%;background:#fff}
.copyright{left:0;top:2150px;width:1200px;text-align:center;color:#fff;font-size:11px}
</style>
</head>
<body>

<header>
  <div class="abs topbar"></div>
  <div class="abs contact-line" style="top:10px">
    <svg viewBox="0 0 24 24"><path fill="#07c9d6" d="M6.6 10.8a15 15 0 0 0 6.6 6.6l2.2-2.2c.3-.3.7-.4 1-.2 1.1.4 2.3.6 3.6.6.6 0 1 .4 1 1V20c0 .6-.4 1-1 1A17 17 0 0 1 3 4c0-.6.4-1 1-1h3.5c.6 0 1 .4 1 1 0 1.3.2 2.5.6 3.6.1.3 0 .7-.2 1z"/></svg>
    (206) 555-0148
  </div>
  <div class="abs contact-line" style="top:44px">
    <svg viewBox="0 0 24 24"><rect x="2" y="5" width="20" height="14" rx="1" fill="#07c9d6"/><path d="M2 6l10 7 10-7" stroke="#fff" stroke-width="1.6" fill="none"/></svg>
    kestrelwaymassage@fernmail.net
  </div>
  <nav class="abs navbar">
    <ul class="nav-links">
      <li class="active">Home</li><li>About Us</li><li>Services</li><li>Education</li><li>Photo Gallery</li><li>Prices</li><li>Contact</li>
    </ul>
  </nav>
  <div class="abs brand-panel"><div class="brand-mark">Kestrel<br>Way</div></div>
</header>

<section>
  <div class="abs hero" role="img" aria-label="Woman relaxing during a hot stone massage with candles"></div>
  <div class="abs hero-title"><div class="w">Massage</div><div class="n">Therapy</div></div>
  <div class="abs hero-rule"></div>
  <div class="abs hero-tag">We Come To You</div>
  <div class="abs hero-arrow" style="left:53px;top:326px"><svg width="14" height="14" viewBox="0 0 14 14"><path d="M9 2L4 7l5 5" stroke="#555" stroke-width="1.6" fill="none"/></svg></div>
  <div class="abs hero-arrow" style="left:1108px;top:326px"><svg width="14" height="14" viewBox="0 0 14 14"><path d="M5 2l5 5-5 5" stroke="#555" stroke-width="1.6" fill="none"/></svg></div>
</section>

<aside class="abs inquiry">
  <h2>Quick Inquiry</h2>
  <p class="lead">Fill out the form below for your Inquiry.</p>
  <div class="field" style="top:92px">Full Name</div>
  <div class="field" style="top:135px">Email Address</div>
  <div class="field" style="top:178px">Phone Number</div>
  <div class="field" style="top:220px">Type of Massage Therapy<span class="select-caret"></span></div>
  <div class="field area" style="top:264px">Briefly Describe Your Massage</div>
  <div class="cta">GET STARTED NOW</div>
  <p class="note">&#128274; Your information will never be shared</p>
</aside>

<section>
  <h2 class="abs about-title">About Us</h2>
  <div class="abs rule" style="left:139px;top:654px;width:558px"><span class="accent"></span></div>
  <p class="abs about-text">Kestrel Way is a Seattle based mobile massage service. Our massage is offered to the community with a goal of facilitating balance within each individual. We specialize in integrated Pain management, and sports/medical massage therapy.</p>
  <div class="abs point" style="top:795px">
    <span class="point-icon"><svg width="18" height="18" viewBox="0 0 18 18"><circle cx="9" cy="5" r="3" fill="#fff"/><path d="M3 16c0-4 3-6 6-6s6 2 6 6z" fill="#fff"/></svg></span>
    <div><h3>Why we stand out?</h3><p>We are a male and female mobile massage team. <b>+More.</b></p></div>
  </div>
  <div class="abs point" style="top:866px">
    <span class="point-icon"><svg width="18" height="18" viewBox="0 0 18 18"><path d="M9 15s-6-4-6-8a3 3 0 0 1 6-1 3 3 0 0 1 6 1c0 4-6 8-6 8z" fill="#fff"/></svg></span>
    <div><h3>Our Passion...</h3><p>Here at Kestrel Way, we have a great passion for Postural Resoration. <b>+More.</b></p></div>
  </div>
  <div class="abs point" style="top:937px">
    <span class="point-icon"><svg width="20" height="18" viewBox="0 0 20 18"><path d="M10 3L1 7l9 4 9-4z" fill="#fff"/><path d="M5 9v4c2 2 8 2 10 0V9l-5 2z" fill="#fff"/></svg></span>
    <div><h3>Our Education...</h3><p>We are both Graduates of Venmora, school of massage therapy. <b>+More.</b></p></div>
  </div>
  <div class="abs btn-view">VIEW ALL</div>
</section>

<section class="abs prices">
  <h2 class="abs section-title">Our Prices</h2>
  <div class="abs rule" style="left:461px;top:82px;width:277px;background:#dff"></div>
  <div class="abs price-card" style="left:144px">
    <h3>1-hour</h3><p class="rate">$75 Introductory Price*</p>
    <p class="kind">Essential therapeutic relief</p>
    <p class="desc">Donec porta nulla nec portitor ornare. Quisque vulputate. Duis eu sollicitudin elit.Fusce hendrerit orci eu elit commodo. ut feugiat</p>
    <div class="badge"><span>1</span></div>
  </div>
  <div class="abs price-card" style="left:455px">
    <h3>1½-hour</h3><p class="rate">$95 Introductory Price*</p>
    <p class="kind">Complete therapeutic relief</p>
    <p class="desc">Donec porta nulla nec portitor ornare. Quisque vulputate. Duis eu sollicitudin elit.Fusce hendrerit orci eu elit commodo. ut feugiat</p>
    <div class="badge"><span>2</span></div>
  </div>
  <div class="abs price-card" style="left:764px">
    <h3>2-hour</h3><p class="rate">$120 Introductory Price*</p>
    <p class="kind">Maximum therapeutic relief</p>
    <p class="desc">Donec porta nulla nec portitor ornare. Quisque vulputate. Duis eu sollicitudin elit.Fusce hendrerit orci eu elit commodo. ut feugiat</p>
    <div class="badge"><span>3</span></div>
  </div>
</section>

<section>
  <h2 class="abs section-title reviews-title">What Client Say About US</h2>
  <div class="abs rule" style="left:415px;top:1581px;width:370px"><span class="accent" style="left:145px;width:80px"></span></div>
  <div class="abs client-photo" role="img" aria-label="Portrait of the client"></div>
  <div class="abs client-name">Jonah Reyes</div>
  <div class="abs client-role">Family Law</div>
  <p class="abs client-quote">The most important thing to 'us', as Licenced providers is to get you on to our table to show you our skills. But a good therapist never forgets that it's not about what we do for you, but what we can facilitate for you.</p>
  <div class="abs dots"><i class="on"></i><i></i><i></i></div>
</section>

<footer>
  <div class="abs footer" role="img" aria-label="Dim spa scene with a massage therapist and candles"></div>
  <div class="abs foot-mark">Kestrel<br>Way</div>
  <ul class="abs foot-nav"><li>HOME</li><li>ABOUT US</li><li>SERVICES</li><li>PHOTO GALLERY</li><li>EDUCATION</li><li>PRICES</li><li>CONTACT</li></ul>
  <div class="abs foot-rule" style="left:384px;top:2019px;width:433px"></div>
  <div class="abs foot-phone">
    <svg width="30" height="30" viewBox="0 0 24 24"><path fill="#d8d8d8" d="M6.6 10.8a15 15 0 0 0 6.6 6.6l2.2-2.2c.3-.3.7-.4 1-.2 1.1.4 2.3.6 3.6.6.6 0 1 .4 1 1V20c0 .6-.4 1-1 1A17 17 0 0 1 3 4c0-.6.4-1 1-1h3.5c.6 0 1 .4 1 1 0 1.3.2 2.5.6 3.6.1.3 0 .7-.2 1z"/></svg>
    (206) 555-0148
  </div>
  <div class="abs foot-rule" style="left:415px;top:2083px;width:370px"></div>
  <div class="abs socials"><i></i><i></i><i></i><i></i></div>
  <p class="abs copyright">Copyright © 2015 Kestrel Way Massage.</p>
</footer>

</body>
</html>
```